Brightmill Data Works

Our company is about IT hardwares and IT solutions. IT hardware such as PC, RAMS, storage and servers. IT solutions such as project management, BA. We are also selling new technology too.

Target Market(s)

Consumer, Small to Medium Business, Corporate

Requirements
Must have
• The business card must have the following:
• Name:
• Title:
• Contact Number:
• Email address:
• Website:
• Color: Must match the logo color upgrade

```html
<!DOCTYPE html>
<html lang="en">
<head>
<meta charset="utf-8">
<title>Brightmill Data Works – Business Card</title>
<link href="https://fonts.googleapis.com/css2?family=Rubik:wght@400;500;600&display=swap" rel="stylesheet">
<style>
  :root {
    --copper-light: #dc9640;
    --copper-dark: #c0632a;
    --ink: #3a3a3c;
    --ink-soft: #4a4a4a;
    --paper: #ffffff;
    --stage: #232323;
  }
  * { margin: 0; padding: 0; box-sizing: border-box; }
  html, body { width: 1200px; height: 930px; overflow: hidden; background: var(--stage); }
  body { position: relative; font-family: "Rubik", sans-serif; }

  .card {
    position: absolute;
    width: 640px;
    height: 370px;
    border-radius: 18px;
    overflow: hidden;
    box-shadow: 0 14px 30px rgba(0,0,0,.45);
  }

  /* Front */
  .card--front {
    left: 110px; top: 70px;
    background: linear-gradient(115deg, var(--copper-light), var(--copper-dark));
    display: flex; align-items: center; justify-content: center;
  }
  .brand-front {
    color: var(--paper);
    font-weight: 600;
    font-size: 42px;
    letter-spacing: 1px;
    text-transform: uppercase;
    text-align: center;
    line-height: 1.15;
  }

  /* Back */
  .card--back { left: 450px; top: 490px; background: var(--paper); }
  .brand-back {
    position: absolute; right: 46px; top: 54px;
    color: var(--ink);
    font-weight: 600;
    font-size: 26px;
    letter-spacing: .5px;
    text-transform: uppercase;
    text-align: right;
    line-height: 1.15;
  }
  .divider {
    position: absolute; left: 260px; right: 46px; top: 160px;
    height: 1.5px; background: var(--ink);
  }
  .person { position: absolute; left: 44px; top: 150px; }
  .person__name {
    color: var(--copper-light);
    font-weight: 500; font-size: 24px;
    text-transform: uppercase;
  }
  .person__title { color: var(--ink-soft); font-size: 16px; margin-top: 2px; display: flex; align-items: center; gap: 10px; }
  .person__title::after { content: ""; width: 150px; height: 1.5px; background: var(--ink); }

  .contact { position: absolute; left: 50px; top: 222px; list-style: none; }
  .contact li { display: flex; align-items: center; gap: 10px; color: var(--ink); font-size: 16px; line-height: 25px; }
  .contact svg { width: 12px; height: 12px; fill: none; stroke: var(--copper-light); stroke-width: 1.8; }
  .contact .accent { color: var(--copper-light); }

  .rule { position: absolute; left: 0; right: 0; bottom: 54px; height: 1.5px; background: var(--ink); }
  .band {
    position: absolute; left: 0; right: 0; bottom: 0; height: 48px;
    background: linear-gradient(100deg, var(--copper-light), var(--copper-dark));
    color: var(--paper);
    font-size: 15px; letter-spacing: .5px;
    display: flex; align-items: center; justify-content: center;
  }
</style>
</head>
<body>
  <section class="card card--front">
    <div class="brand-front">Brightmill<br>Data Works</div>
  </section>

  <section class="card card--back">
    <div class="brand-back">Brightmill<br>Data Works</div>
    <div class="divider"></div>

    <div class="person">
      <div class="person__name">Daniel Harlow</div>
      <div class="person__title">Director</div>
    </div>

    <ul class="contact">
      <li>
        <svg viewBox="0 0 12 12"><path d="M2.5 1.5 L4.5 1.5 L5 4 L3.8 5 Q5 7.5 7 8.2 L8 7 L10.5 7.5 L10.5 9.5 Q10 11 8 10.5 Q3 9 1.5 4 Q1 2 2.5 1.5 Z"/></svg>
        555-214-7730
      </li>
      <li>
        <svg viewBox="0 0 12 12"><rect x="1" y="2.5" width="10" height="7"/><path d="M1 2.5 L6 6.5 L11 2.5"/></svg>
        info@brightmilldata.com
      </li>
      <li>
        <svg viewBox="0 0 12 12"><circle cx="6" cy="6" r="5"/><ellipse cx="6" cy="6" rx="2.2" ry="5"/><path d="M1 6 H11"/></svg>
        <span>www.<span class="accent">brightmilldata</span>.com</span>
      </li>
    </ul>

    <div class="rule"></div>
    <div class="band">220 Orchard Lane Fairview, CA 90210-4417</div>
  </section>
</body>
</html>
```